Kestal-Materials. Limestone; improving the world

New Limestone company and need logo design.
Limestone offsets carbon mitigation industries restore and replenish soil fertilities in the Prairies, the breadbasket of the world. At the same time, Limestone is proving a critical emergent component of carbon capture sequestration technology will therefore play a critical role in the development of the western Canadian energy industries
Our limestone resources are situated in the foothills of the Canadian Rockies well-positioned above the sprawling fields of the vast peace district.
Agriculture and oli sites
Kestal Materials
3 page

```html
<!DOCTYPE html>
<html lang="en">
<head>
<meta charset="utf-8">
<title>Kestal Materials</title>
<link href="https://fonts.googleapis.com/css2?family=Roboto:wght@400;500;700&family=Lato:wght@400;700&display=swap" rel="stylesheet">
<style>
:root{
  --blue:#3a8fc8;
  --blue-dark:#2f7bb0;
  --ink:#222;
  --text:#444;
  --navy:#30496a;
  --footer:#1b1b1c;
  --white:#fff;
  --rule:#3a8fc8;
}
*{box-sizing:border-box;margin:0;padding:0}
html,body{width:1200px;height:4601px;overflow:hidden;background:#fff}
body{font-family:'Lato',sans-serif;color:var(--text);position:relative}
section,header,footer{position:absolute;left:0;width:1200px}
.abs{position:absolute}
.btn{position:absolute;background:var(--blue);color:#fff;font-family:'Roboto',sans-serif;font-weight:500;font-size:14.5px;letter-spacing:.5px;display:flex;align-items:center;justify-content:center;border-radius:2px}
.btn-outline{position:absolute;border:2px solid var(--blue);color:var(--blue);font-family:'Roboto',sans-serif;font-weight:700;font-size:13px;display:flex;align-items:center;justify-content:center;border-radius:2px;background:#fff}
h2{font-family:'Roboto',sans-serif;font-weight:500}
.rule{position:absolute;height:4px;width:64px;background:var(--rule)}

/* header */
.site-header{top:0;height:91px;background:#fff}
.brand{left:145px;top:28px;font-family:'Roboto',sans-serif;font-weight:700;font-size:26px;color:#2d4a6b;letter-spacing:-.5px}
.nav{right:145px;top:37px;display:flex;gap:23px;font-family:'Roboto',sans-serif;font-weight:500;font-size:13.5px;color:#222}
.nav .active{color:var(--blue)}

/* hero */
.hero{top:91px;height:666px;background:linear-gradient(135deg,#b9a58e,#cdbba5 45%,#a8947c)}
.hero-map{left:40px;top:90px;width:1120px;height:440px;border-radius:40%;background:radial-gradient(ellipse at center,#4f8a34 0%,#3e7a2a 45%,rgba(80,130,50,0) 72%)}
.hero-title{width:100%;top:212px;text-align:center;font-family:'Roboto',sans-serif;font-weight:700;font-size:58px;color:#fff;text-shadow:0 2px 6px rgba(0,0,0,.35)}
.hero-sub{width:100%;top:286px;text-align:center;font-family:'Roboto',sans-serif;font-weight:300;font-size:38px;color:#fff;text-shadow:0 2px 6px rgba(0,0,0,.35)}
.hero .btn{left:497px;top:361px;width:207px;height:43px}
.dots{left:561px;top:609px;display:flex;gap:6px}
.dots span{width:14px;height:14px;border-radius:50%;border:2px solid #333}
.dots span.on{background:#49b3c4;border-color:#2a6f7a}

/* about */
.about{top:757px;height:547px}
.about-media{left:145px;top:98px;width:498px;height:351px;border:5px solid #fff;box-shadow:0 4px 14px rgba(0,0,0,.22);background:linear-gradient(160deg,#b9c86a,#6d8c3a 40%,#d9dcd6 70%,#f2f2ef)}
.about-media svg{position:absolute;left:216px;top:143px}
.about h2{left:688px;top:100px;font-size:40px;color:var(--ink)}
.about .rule{left:688px;top:165px;width:98px;height:2px}
.about p{left:688px;top:185px;width:370px;font-size:16.3px;line-height:23.3px;color:#333}
.about .btn{left:688px;top:391px;width:150px;height:43px}

/* products */
.products{top:1304px;height:825px;background:linear-gradient(180deg,#3e5676,#2d4565 50%,#2a3f5b)}
.products h2{width:100%;top:72px;text-align:center;font-size:38px;color:#fff}
.products .rule{left:568px;top:135px;background:#fff;height:3px}
.products .lead{left:190px;top:168px;width:820px;text-align:center;font-size:18px;line-height:27.5px;color:#fff}
.card{position:absolute;top:307px;width:291px;height:409px;background:#fff;border-radius:8px;text-align:center}
.card .icon{position:absolute;left:84px;top:36px;width:122px;height:122px;border-radius:50%;background:#2e5b80;border:5px solid #b7d5e6}
.card h3{position:absolute;top:182px;width:100%;font-family:'Roboto',sans-serif;font-weight:500;font-size:19.5px;color:#2f6fa0}
.card p{position:absolute;top:221px;left:20px;width:251px;font-size:14.5px;line-height:21.5px;color:#444}
.card .btn-outline{left:78px;top:329px;width:134px;height:37px}

/* sustainability */
.sustain{top:2129px;height:607px;background:linear-gradient(100deg,#334e66 0%,#5d7b95 30%,#e7b873 55%,#9fb7c8 75%,#6e8f6a 100%)}
.sustain-panel{left:145px;top:116px;width:450px;height:400px;background:rgba(255,255,255,.93)}
.sustain h2{left:25px;top:30px;font-size:40px;color:var(--ink);font-weight:700}
.sustain .rule{left:25px;top:94px;width:100px;height:2px}
.sustain p{left:25px;top:124px;width:400px;font-size:15px;line-height:21.4px;color:#333}
.sustain .btn{left:26px;top:311px;width:167px;height:43px}

/* news */
.news{top:2736px;height:720px}
.news h2{width:100%;top:62px;text-align:center;font-size:38px;color:var(--ink)}
.news .rule{left:568px;top:121px;height:3px;width:80px}
.post{position:absolute;top:166px;width:286px;height:461px;background:#fff;box-shadow:0 3px 12px rgba(0,0,0,.15)}
.post .thumb{height:200px}
.post .date{position:absolute;left:21px;top:227px;font-family:'Roboto',sans-serif;font-size:12.5px;color:var(--blue);display:flex;align-items:center;gap:6px}
.post h3{position:absolute;left:21px;top:259px;width:250px;font-family:'Roboto',sans-serif;font-weight:700;font-size:13.5px;line-height:20px;color:#222}
.post p{position:absolute;left:21px;top:313px;width:250px;font-size:14px;line-height:19.5px;color:#555}
.post .more{position:absolute;left:21px;top:415px;font-family:'Roboto',sans-serif;font-weight:500;font-size:13.5px;color:var(--blue);display:flex;align-items:center;gap:7px}

/* testimonials */
.testimonials{top:3456px;height:605px;background:linear-gradient(160deg,#2f7ab5,#3d8fc8 50%,#4c9bcf)}
.testimonials h2{width:100%;top:62px;text-align:center;font-size:40px;color:#fff}
.quote{position:absolute;top:196px;width:415px;height:318px;border:2px solid rgba(255,255,255,.85);border-radius:8px}
.quote .mark{position:absolute;left:-22px;top:8px;font-family:Georgia,serif;font-size:90px;line-height:1;color:#fff}
.quote p{position:absolute;left:40px;top:42px;width:345px;font-size:15.3px;line-height:24.5px;color:#fff}
.quote .who{position:absolute;left:40px;top:236px;font-size:16px;color:#fff}
.quote .stars{position:absolute;left:40px;top:268px;color:#ffd21e;font-size:16px;letter-spacing:1px}
.arrow{position:absolute;top:326px}

/* footer */
.site-footer{top:4061px;height:540px;background:var(--footer);color:#fff}
.col{position:absolute;top:67px}
.col h4{font-family:'Roboto',sans-serif;font-weight:700;font-size:17.5px;letter-spacing:.3px;margin-bottom:18px}
.col ul{list-style:none}
.col li{font-size:13.5px;line-height:27.3px;color:#e6e6e6}
.contact-item{display:flex;gap:14px;font-size:13.5px;line-height:24px;color:#e6e6e6;margin-bottom:9px}
.contact-item svg{flex:none;margin-top:4px}
.socials{display:flex;gap:11px;margin-top:10px}
.socials span{width:38px;height:38px;border:2px solid #fff;border-radius:50%}
.copyright{position:absolute;width:100%;top:458px;text-align:center;font-size:14px;color:#e6e6e6}
</style>
</head>
<body>

<header class="site-header">
  <div class="abs brand">Kestal Materials</div>
  <nav class="abs nav">
    <span class="active">HOME</span><span>ABOUT US</span><span>PRODUCTS</span><span>SUSTAINABILITY</span><span>CAREERS</span><span>CONTACT</span>
  </nav>
</header>

<section class="hero">
  <div class="abs hero-map" role="img" aria-label="World map made of green plants on a light wooden surface with faint eco icons"></div>
  <div class="abs hero-title">Kestal Materials</div>
  <div class="abs hero-sub">We are a New Limestone company</div>
  <div class="btn">CUSTOMER PORTAL</div>
  <div class="abs dots"><span class="on"></span><span></span><span></span><span></span></div>
</section>

<section class="about">
  <div class="abs about-media" role="img" aria-label="Laptop and glasses on a desk outdoors with trees behind">
    <svg width="60" height="60" viewBox="0 0 60 60"><circle cx="30" cy="30" r="27" fill="rgba(255,255,255,.15)" stroke="#fff" stroke-width="3"/><path d="M24 18 L42 30 L24 42 Z" fill="none" stroke="#fff" stroke-width="3"/></svg>
  </div>
  <h2 class="abs">Who We Are</h2>
  <div class="rule"></div>
  <p class="abs">Lorem ipsum dolor sit amet, consectetur adipiscing elit, sed do eiusmod tempor incididunt ut labore et dolore magna aliqua. Ut enim ad minim veniam, quis nostrud exercitation ullamco laboris nisi ut aliquip ex ea commodo consequat. Duis aute irure dolor in rehenderit in voluptate velit esse cillum dolore eu fugiat nulla pariatur. Excepteur sint occaecat cupidatat non proident, sunt in culpa</p>
  <div class="btn">LEARN MORE</div>
</section>

<section class="products">
  <h2 class="abs">Our Products</h2>
  <div class="rule"></div>
  <p class="abs lead">Kestal Materials extensive product offering includes high-calcium and dolomitic lime, along with value-added lime-based products such as specialty hydrates, as well as pulverized stone and construction stone.</p>
  <div class="card" style="left:145px">
    <div class="icon" role="img" aria-label="Chemical limestone rock icon"></div>
    <h3>Chemical Limestone</h3>
    <p>Sed ut perspiciatis unde omnis iste natus error sit voluptatem accsantium dmque laudantium, totam rem aperiam, eaque ipsa</p>
    <div class="btn-outline">LEARN MORE</div>
  </div>
  <div class="card" style="left:455px">
    <div class="icon" role="img" aria-label="Construction worker with stone blocks icon"></div>
    <h3>Construction Stone</h3>
    <p>Sed ut perspiciatis unde omnis iste natus error sit voluptatem accsantium dmque laudantium, totam rem aperiam, eaque ipsa</p>
    <div class="btn-outline">LEARN MORE</div>
  </div>
  <div class="card" style="left:764px">
    <div class="icon" role="img" aria-label="Pulverized limestone pieces icon"></div>
    <h3>Pulverized Limestone</h3>
    <p>Sed ut perspiciatis unde omnis iste natus error sit voluptatem accsantium dmque laudantium, totam rem aperiam, eaque ipsa</p>
    <div class="btn-outline">LEARN MORE</div>
  </div>
</section>

<section class="sustain" role="img" aria-label="City skyline at sunrise with green trees and a glass walkway">
  <div class="abs sustain-panel">
    <h2 class="abs">Sustainability</h2>
    <div class="rule"></div>
    <p class="abs">Lorem ipsum dolor sit amet, consectetur adipiscing elit, sed do eiusmod tempor incididunt ut labore et dolore magna aliqua. Ut enim ad minim veniam, quis nostrud exercitation ullamco laboris nisi ut aliquip ex ea commodo consequat. Duis aute irure dolor in rehenderit in voluptate velit esse cillum dolore eu fugiat nulla pariatur. Excepteur sint occaecat cupidatat non proident, sunt in culpa qui officia deserunt mollit anim id est laborum</p>
    <div class="btn">LEARN MORE</div>
  </div>
</section>

<section class="news">
  <h2 class="abs">Latest News</h2>
  <div class="rule"></div>
  <article class="post" style="left:145px">
    <div class="thumb" role="img" aria-label="Double exposure of an engineer and city buildings" style="background:linear-gradient(180deg,#8a94a0,#d2d6da)"></div>
    <div class="date"><svg width="12" height="12" viewBox="0 0 12 12"><rect x="1" y="2" width="10" height="9" rx="1" fill="#3a8fc8"/><rect x="1" y="4" width="10" height="1" fill="#fff"/></svg>MARCH 09, 2021</div>
    <h3>NEMO ENIM IPSAM VOLUPTATEM QUIA VOLUPTAS SIT</h3>
    <p>Sed ut perspiciatis unde omnis iste natus error sit voluptatem accusaium dremque laudantium, totam rem aiam, eaque ipsa quae ab illo inveore vetatis et quasi architecto beatae</p>
    <div class="more">LEARN MORE <svg width="12" height="10" viewBox="0 0 12 10"><path d="M1 5H10M6 1L10 5L6 9" stroke="#3a8fc8" stroke-width="2" fill="none"/></svg></div>
  </article>
  <article class="post" style="left:457px">
    <div class="thumb" role="img" aria-label="Two colleagues working at a computer in an office" style="background:linear-gradient(180deg,#a7805f,#d8d0c4)"></div>
    <div class="date"><svg width="12" height="12" viewBox="0 0 12 12"><rect x="1" y="2" width="10" height="9" rx="1" fill="#3a8fc8"/><rect x="1" y="4" width="10" height="1" fill="#fff"/></svg>MARCH 09, 2021</div>
    <h3>NEMO ENIM IPSAM VOLUPTATEM QUIA VOLUPTAS SIT</h3>
    <p>Sed ut perspiciatis unde omnis iste natus error sit voluptatem accusaium dremque laudantium, totam rem aiam, eaque ipsa quae ab illo inveore vetatis et quasi architecto beatae</p>
    <div class="more">LEARN MORE <svg width="12" height="10" viewBox="0 0 12 10"><path d="M1 5H10M6 1L10 5L6 9" stroke="#3a8fc8" stroke-width="2" fill="none"/></svg></div>
  </article>
  <article class="post" style="left:768px">
    <div class="thumb" role="img" aria-label="Smiling construction worker in a yellow hard hat" style="background:linear-gradient(180deg,#5c6470,#9aa3ad)"></div>
    <div class="date"><svg width="12" height="12" viewBox="0 0 12 12"><rect x="1" y="2" width="10" height="9" rx="1" fill="#3a8fc8"/><rect x="1" y="4" width="10" height="1" fill="#fff"/></svg>MARCH 09, 2021</div>
    <h3>NEMO ENIM IPSAM VOLUPTATEM QUIA VOLUPTAS SIT</h3>
    <p>Sed ut perspiciatis unde omnis iste natus error sit voluptatem accusaium dremque laudantium, totam rem aiam, eaque ipsa quae ab illo inveore vetatis et quasi architecto beatae</p>
    <div class="more">LEARN MORE <svg width="12" height="10" viewBox="0 0 12 10"><path d="M1 5H10M6 1L10 5L6 9" stroke="#3a8fc8" stroke-width="2" fill="none"/></svg></div>
  </article>
</section>

<section class="testimonials" role="img" aria-label="Blue-tinted field of wind turbines">
  <h2 class="abs">What Our Customers Say</h2>
  <svg class="arrow" style="left:95px" width="24" height="36" viewBox="0 0 24 36"><path d="M20 3L5 18L20 33" stroke="#fff" stroke-width="4" fill="none"/></svg>
  <div class="quote" style="left:175px">
    <div class="mark">&ldquo;</div>
    <p>Sed ut perspiciatis unde omnis iste natus error sit voluptatem accusantium doloremque laudantium, totam rem aperiam, eaque ipsa quae ab illo inventore veritatis et quasi architecto beatae vitae dicta sunt explicabo. Nemo enim ipsam voluptatem quia voluptas sit aspernatur aut odit aut fugit, sed quia</p>
    <div class="who">Tomas Verhallen - Kestal Materials</div>
    <div class="stars">★★★★★</div>
  </div>
  <div class="quote" style="left:630px">
    <div class="mark">&ldquo;</div>
    <p>Sed ut perspiciatis unde omnis iste natus error sit voluptatem accusantium doloremque laudantium, totam rem aperiam, eaque ipsa quae ab illo inventore veritatis et quasi architecto beatae vitae dicta sunt explicabo. Nemo enim ipsam voluptatem quia voluptas sit aspernatur</p>
    <div class="who">Arlen Dussault - Kestal Materials</div>
    <div class="stars">★★★★★</div>
  </div>
  <svg class="arrow" style="left:1080px" width="24" height="36" viewBox="0 0 24 36"><path d="M4 3L19 18L4 33" stroke="#fff" stroke-width="4" fill="none"/></svg>
</section>

<footer class="site-footer">
  <div class="col" style="left:145px;width:320px">
    <h4>CONTACT US</h4>
    <div class="contact-item"><svg width="16" height="18" viewBox="0 0 16 18"><path d="M8 17C8 17 2 10.5 2 7A6 6 0 0 1 14 7C14 10.5 8 17 8 17Z" stroke="#fff" stroke-width="1.5" fill="none"/><circle cx="8" cy="7" r="2" fill="#fff"/></svg><span>6021 enim ipsam voluptatem<br>quia voluptas</span></div>
    <div class="contact-item"><svg width="16" height="16" viewBox="0 0 16 16"><path d="M3 1L6 1L7 5L5 6.5C6 8.5 7.5 10 9.5 11L11 9L15 10L15 13C15 14 14 15 13 15C6.5 15 1 9.5 1 3C1 2 2 1 3 1Z" stroke="#fff" stroke-width="1.4" fill="none"/></svg><span>Phone: 555 0142 7700</span></div>
    <div class="contact-item"><svg width="16" height="16" viewBox="0 0 16 16"><rect x="1" y="5" width="14" height="9" fill="#fff"/><rect x="4" y="1" width="8" height="4" fill="none" stroke="#fff" stroke-width="1.4"/><rect x="4" y="9" width="8" height="2" fill="#1b1b1c"/></svg><span>Fax: 555 0142 7700</span></div>
    <div class="contact-item"><svg width="16" height="14" viewBox="0 0 16 14"><rect x="1" y="2" width="14" height="10" fill="none" stroke="#fff" stroke-width="1.4"/><path d="M1 2L8 8L15 2" stroke="#fff" stroke-width="1.4" fill="none"/></svg><span>Email: info@kestalmaterials.com</span></div>
    <div class="socials"><span></span><span></span><span></span></div>
  </div>
  <div class="col" style="left:488px">
    <h4>QUICK LINKS</h4>
    <ul><li>Home</li><li>Products</li><li>Markets</li><li>Sustainability</li><li>About Us</li><li>Careers</li><li>Contact Us</li><li>Customer Portal</li></ul>
  </div>
  <div class="col" style="left:680px">
    <h4>PRODUCTS</h4>
    <ul><li>Quicklime</li><li>Hydrated Lime</li><li>Pulverized Limestone</li><li>Chemical Limestone</li><li>Construction Stone</li><li>Co-products</li><li>Safety Data Sheets (SDS)</li><li>Technical Information</li></ul>
  </div>
  <div class="col" style="left:897px">
    <h4>SUSTAINABILITY</h4>
    <ul><li>Our Commitment</li><li>Environmental Care</li><li>Workforce Culture</li><li>Community Relations</li><li>Transparency</li><li>Sustainability Reports</li></ul>
  </div>
  <div class="copyright">(c) 2021 Kestal Materials | All Rights Reserved</div>
</footer>

</body>
</html>
```